Progressive European Honey Business needs minimalistic packaging design

Hello - thank you for your interest in our brief. We are Honey Plinks, a London based Honey business, importing only the best honey Europe has to offer. Our values are deeply rooted with in progressive liberal values and we are looking for minimalist packaging, which reflects that.

We are looking for a design, which dimensions fit with our packaging option (Vessio Glass Jar | HEIGHT 90mm | DIAMETER 63mm). We will require a various output files (High Resolution JPEG (CMYK Colors 300 dpi) Source File Ai, PSD, PDF, Printing files (die cut, die folding) and a 3D Mockup of the packaging for use within digital commerce platforms.

We must be able to adjust the free text on the label front and it should include the following:
Brand Name
Honey type
Limited edition No. X / 100 ( X being the number of purchase i.e. 25 / 100)
EU Honey, Single Orgin (Germany)
(c) The net weight (250g)

The back must include room for additional information (again adjustable by us) and the following:
“Unsuitable for children under 12 months”
(b) The appropriate durability declaration

In total, we are looking for
a) A front label
b) A back label
c) A seal (round) including the attached bee and logo included in the Zip file.
Do note that a) & b) can also be combined into one design as long as the symmetry on the jar stays intact.

The final design should communicate modern aesthetics, high quality, that are slightly provocative and pop off the shelves.

Hi folks, sorry for the delay in completing this project, but my business partner had a leak in his house. We planned to finalise our review today, but this will have to wait until it's no longer raining in his livingroom. Our sincere apologies!

• See branding guidelines

• Must follow the branding guideline and fonts provided as attachment

```html
<!DOCTYPE html>
<html lang="en">
<head>
<meta charset="utf-8">
<title>Honey Plinks – Front Label</title>
<link rel="stylesheet" href="https://fonts.googleapis.com/css2?family=Lexend:wght@300;400;600;700;800&display=swap">
<style>
  :root {
    --stage: #f4f4f4;
    --label: #ffffff;
    --comb: #f7f7f7;
    --orange: #ec6a2c;
    --ink: #1a1a1a;
  }
  * { box-sizing: border-box; margin: 0; padding: 0; }
  html, body {
    width: 1200px; height: 750px; overflow: hidden;
    background: var(--stage);
    font-family: "Lexend", sans-serif;
    color: var(--ink);
  }
  .canvas {
    position: relative; width: 1200px; height: 750px;
    display: flex; align-items: center; justify-content: center;
  }
  .front-label {
    position: relative; width: 370px; height: 540px;
    background: var(--label);
    box-shadow: 0 6px 24px rgba(0,0,0,0.08);
  }
  .label-texture {
    position: absolute; inset: 0; width: 100%; height: 100%;
  }
  .label-frame {
    position: absolute; left: 29px; top: 30px;
    width: 326px; height: 480px;
    border: 6px solid var(--orange);
  }
  .frame-item {
    position: absolute; left: 0; right: 0;
    transform: translateY(-50%);
    display: flex; justify-content: center; align-items: center;
    text-align: center; white-space: nowrap;
  }
  .brand-name {
    top: 133px;
    font-weight: 800; font-size: 32px; letter-spacing: 0.5px; line-height: 1;
    color: var(--orange); text-transform: uppercase;
  }
  .honey-type {
    top: 246px;
    font-weight: 700; font-size: 45px; letter-spacing: -0.5px; line-height: 1;
  }
  .origin-row { top: 321px; }
  .origin-eu { text-align: left; padding-right: 11px; }
  .origin-eu-title { font-weight: 600; font-size: 17px; line-height: 1; }
  .origin-eu-sub { font-weight: 300; font-size: 8.5px; letter-spacing: 2.2px; margin-top: 2px; line-height: 1; }
  .origin-divider { width: 1px; height: 68px; background: var(--ink); }
  .origin-country { padding-left: 13px; font-weight: 300; font-size: 17px; line-height: 1; }
  .edition {
    top: 392px; gap: 3px;
    font-weight: 300; font-size: 12px; letter-spacing: 3.4px; line-height: 1;
  }
  .edition-number {
    background: var(--ink); color: #fff; letter-spacing: 0;
    font-weight: 600; font-size: 10px; line-height: 1;
    padding: 8px 8px; border-radius: 14px;
  }
  .net-weight { top: 438px; flex-direction: column; line-height: 1; }
  .net-weight-value { font-weight: 600; font-size: 13px; }
  .net-weight-caption { font-weight: 300; font-size: 8.5px; letter-spacing: 2px; margin-top: 1px; }
</style>
</head>
<body>
<main class="canvas">
  <section class="front-label">
    <svg class="label-texture" role="img" aria-label="Faint honeycomb pattern across the label background" viewBox="0 0 370 540" preserveAspectRatio="none">
      <rect width="370" height="540" fill="var(--comb)"/>
    </svg>
    <div class="label-frame">
      <h1 class="frame-item brand-name">Honey Plinks</h1>
      <h2 class="frame-item honey-type">Honey type</h2>
      <div class="frame-item origin-row">
        <div class="origin-eu">
          <div class="origin-eu-title">EU HONEY</div>
          <div class="origin-eu-sub">SINGLE ORIGIN</div>
        </div>
        <span class="origin-divider"></span>
        <div class="origin-country">Germany</div>
      </div>
      <div class="frame-item edition">
        <span>Limited edition No.</span>
        <span class="edition-number">25/100</span>
      </div>
      <div class="frame-item net-weight">
        <div class="net-weight-value">(250g)</div>
        <div class="net-weight-caption">Net Weight</div>
      </div>
    </div>
  </section>
</main>
</body>
</html>
```